Stationery Design Project for Strelvane, Chicago

Strelvane, a street parking application which helps car drivers find a street parking spot by offering an ideal path along which to look for parking. This path is calculated by our algorithm based on data (e.g. historical data, baseball games schedule, etc.). Along this path the driver will find a spot and will also save 70% of the search time. Customer we target is reg. between 21 and 45 yo.

We envision something young, fresh, bright and original. Slightly abstract maybe. It should represent the idea and elements of finding street parking in the city, e.g. car(s), parking spot, people, city, etc. (just ideas!).

Logo is attached.

Requirement:
- Business Cards (2 Sided Full Color CMYK)
- Letterhead (1 Sided Full Color CMYK)
- Envelope (1 Sided Full Color CMYK)
- Sticker (1 Sided Full Color CMYK), round with a 2inch diameter.

Reason: We're starting to get more and more designs and need more time to look into all of them. Very exciting!! Thanks to everybody!

Hi all, we're in the process of selecting our favs. Though choices!!! Really good submissions. Will keep you posted and sorry for the delay.

Target Market(s)

Car drivers and owners between 21 and 45

Industry/Entity Type

Parking

Requirements
Must have
• Sticker should be round and include company URL strelvane.com and the new logo which we will attach soon.
Should not have
• Should not be too serious or boring.

```html
<!DOCTYPE html>
<html lang="en">
<head>
<meta charset="utf-8">
<title>Strelvane – Business Card</title>
<link rel="stylesheet" href="https://fonts.googleapis.com/css2?family=Open+Sans:wght@400;600;700&display=swap">
<style>
  :root {
    --page-bg: #e6e6e6;
    --card-bg: #ffffff;
    --brand-blue: #283593;
    --brand-navy: #2b3990;
    --accent-sky: #29a9e0;
    --ink: #1c1c1c;
    --text-grey: #555555;
    --strip-grey: #8a8a8a;
    --strip-dark: #111111;
    --swoosh: #f0f0f2;
    --halo: #f2f2f4;
    --icon: #ffffff;
  }
  * { margin: 0; padding: 0; box-sizing: border-box; }
  html, body { width: 954px; height: 1200px; overflow: hidden; }
  body {
    background: var(--page-bg);
    font-family: "Open Sans", Arial, sans-serif;
    position: relative;
  }
  .card {
    position: absolute;
    left: 74px;
    width: 796px;
    height: 455px;
    background: var(--card-bg);
    border-radius: 28px;
    overflow: hidden;
    box-shadow: 0 3px 8px rgba(0,0,0,0.25);
  }
  .card--front { top: 125px; }
  .card--back { top: 656px; }
  .card__swoosh { position: absolute; left: 0; top: 0; }
  .card__edge-strip {
    position: absolute; left: 728px; top: 0; width: 6px; height: 100%;
    background: var(--strip-grey);
  }
  .card__edge-strip::after {
    content: ""; position: absolute; left: 0; top: 150px; width: 6px; height: 155px;
    background: var(--strip-dark);
  }
  .card__band {
    position: absolute; left: 734px; top: 0; width: 62px; height: 100%;
    background: var(--brand-blue);
  }
  .brand { position: absolute; left: 42px; top: 45px; height: 170px; display: flex; align-items: center; }
  .brand__dot {
    width: 160px; height: 160px; border-radius: 50%;
    background: radial-gradient(circle at 50% 45%, #2a8fe0, #1f3f9e);
    box-shadow: 0 0 0 6px var(--halo);
  }
  .brand__name {
    margin-left: 29px; font-size: 94px; font-weight: 600; color: var(--ink);
    letter-spacing: -1px; line-height: 1;
    position: relative; top: 4px;
  }
  .holder { position: absolute; left: 54px; top: 258px; font-weight: 700; }
  .holder__name { font-size: 24px; color: var(--brand-navy); }
  .holder__role { font-size: 19px; color: var(--accent-sky); }
  .address {
    position: absolute; left: 42px; top: 372px; display: flex; align-items: flex-start;
    font-size: 19px; line-height: 27px; color: var(--text-grey);
  }
  .address svg { margin: 6px 10px 0 0; }
  .contact {
    position: absolute; right: 80px; text-align: right;
    font-size: 19px; line-height: 33px; color: var(--text-grey);
  }
  .contact--phones { top: 228px; }
  .contact--web { top: 363px; }
  .icons { position: absolute; left: 742px; width: 22px; }
  .icons svg { display: block; margin-bottom: 17px; }
  .icons--phones { top: 235px; }
  .icons--web { top: 370px; }
</style>
</head>
<body>

<section class="card card--front">
  <svg class="card__swoosh" width="796" height="455" aria-hidden="true">
    <path d="M470 455 C600 330 650 180 690 0 L712 0 C680 190 630 340 505 455 Z" fill="var(--swoosh)"/>
    <path d="M540 455 C640 350 690 200 720 40 L728 40 L728 200 C700 320 650 400 580 455 Z" fill="var(--swoosh)"/>
  </svg>
  <div class="card__edge-strip"></div>
  <div class="card__band"></div>

  <div class="brand">
    <div class="brand__dot"></div>
    <span class="brand__name">strelvane</span>
  </div>

  <p class="holder"><span class="holder__name">Your Name -</span> <span class="holder__role">Designation</span></p>

  <div class="address">
    <svg width="18" height="16" viewBox="0 0 18 16" aria-hidden="true"><path d="M9 0 L18 8 H15 V16 H11 V11 H7 V16 H3 V8 H0 Z" fill="var(--text-grey)"/></svg>
    <p>City Name, Street Name<br>State Name, Country Code</p>
  </div>

  <p class="contact contact--phones">123-456-7890<br>123-456-7890</p>
  <p class="contact contact--web">name@website.com<br>www.website.com</p>

  <div class="icons icons--phones">
    <svg width="20" height="16" viewBox="0 0 20 16" aria-hidden="true"><path d="M1 5 C1 1 19 1 19 5 L19 7 L14 7 L14 5 L6 5 L6 7 L1 7 Z M4 8 H16 L18 15 H2 Z" fill="var(--icon)"/></svg>
    <svg width="14" height="20" viewBox="0 0 14 20" aria-hidden="true"><rect x="2" y="3" width="10" height="17" rx="2" fill="var(--icon)"/><rect x="9" y="0" width="2" height="4" fill="var(--icon)"/><rect x="4" y="5" width="6" height="4" fill="var(--brand-blue)"/></svg>
  </div>
  <div class="icons icons--web">
    <svg width="18" height="18" viewBox="0 0 18 18" aria-hidden="true"><text x="9" y="15" text-anchor="middle" font-family="Arial, sans-serif" font-weight="700" font-size="17" fill="var(--icon)">@</text></svg>
    <svg width="16" height="16" viewBox="0 0 16 16" aria-hidden="true"><circle cx="8" cy="8" r="7" fill="var(--icon)"/><path d="M1 8 H15 M8 1 C4 5 4 11 8 15 M8 1 C12 5 12 11 8 15" stroke="var(--brand-blue)" stroke-width="1" fill="none"/></svg>
  </div>
</section>

<section class="card card--back">
  <svg class="card__swoosh" width="796" height="455" aria-hidden="true">
    <path d="M470 455 C600 330 650 180 690 0 L712 0 C680 190 630 340 505 455 Z" fill="var(--swoosh)"/>
    <path d="M540 455 C640 350 690 200 720 40 L728 40 L728 200 C700 320 650 400 580 455 Z" fill="var(--swoosh)"/>
  </svg>
  <div class="card__edge-strip"></div>
  <div class="card__band"></div>

  <div class="brand">
    <div class="brand__dot"></div>
    <span class="brand__name">strelvane</span>
  </div>

  <p class="contact contact--web">name@website.com<br>www.website.com</p>

  <div class="icons icons--web">
    <svg width="18" height="18" viewBox="0 0 18 18" aria-hidden="true"><text x="9" y="15" text-anchor="middle" font-family="Arial, sans-serif" font-weight="700" font-size="17" fill="var(--icon)">@</text></svg>
    <svg width="16" height="16" viewBox="0 0 16 16" aria-hidden="true"><circle cx="8" cy="8" r="7" fill="var(--icon)"/><path d="M1 8 H15 M8 1 C4 5 4 11 8 15 M8 1 C12 5 12 11 8 15" stroke="var(--brand-blue)" stroke-width="1" fill="none"/></svg>
  </div>
</section>

</body>
</html>
```